Web design for Crowdfunding site HopeWingsRally.com

We need a web design for christian crowdfunding website. Here is the challenge: We need responsive layout that is targeted first in iPad size of screen. It should also scale somehow down to iPhone size of screens. Web layout can be about the same size as iPad screen.

Screens should work so that main page scrolls not but only certain part of the screen scrolls and always one "page" at time. We can implement these "scrolls" then later with javascript but now we need only design. The challenge is to create this kind of hybrid website / app look.

Target is at first to raise funds to orphan people needing about $40 per month for their living and education. There is always some organization which takes care of these kids. Later there will be other christian missions included. At first we are looking to find monthly supporters.

You can be as creative as you want :) As you see from the look and feel sector, I am not looking any same traditional look which many "help kids" sites have. I am looking to reach now younger generation and therefore iPad and mobile are the main screen sizes.

Inspirational designs:
- https://example-gallery.test/profiles/studiofernlake/designs/482716?from=%2Fbrowse%2Fxhr%2Fdesigns%3Fcategory%3Dmobile-app-design
- http://www.artpoolhub.test/design/8261047 Clear, simple visuals
- http://www.artpoolhub.test/design/7394215 Header
- http://www.artpoolhub.test/design/6048392 Contrast in the colors, i think is powerfull

Some terms could be: Kids play, kids are learning (in the school). No static posture but living like kids are. I wonder also how we could also add little bit gaming style even though the question is of reali life of real people. Giving should be rewarding.

Target Market(s)

People who want help other people.

Industry/Entity Type

Christian

Number of Pages Required

4 page

Requirements
Must have
• Homepage. Mission page (In my wireframes it was one kid).
Nice to have
• Other pages and some idea how to scroll. 4 pages is no must. If you feel easy, please give first some draft and I give comments on that.

```html
<!DOCTYPE html>
<html lang="en">
<head>
<meta charset="utf-8">
<title>HopeWingsRally – Mission: Orphan Maria, 11Y</title>
<link href="https://fonts.googleapis.com/css2?family=Roboto+Condensed:ital,wght@0,400;0,700;1,400&family=Open+Sans:ital,wght@0,400;0,600;1,400&display=swap" rel="stylesheet">
<style>
:root{
  --yellow:#ffc400;
  --dark:#2b2b2b;
  --text:#444;
  --muted:#777;
  --line:#e6e6e6;
  --panel:#f3f3f3;
  --accent-red:#b33a2a;
  --white:#fff;
}
*{box-sizing:border-box;margin:0;padding:0}
html,body{width:1120px;height:1200px;overflow:hidden}
body{position:relative;background:var(--white);font-family:"Open Sans",sans-serif;color:var(--text)}
.abs{position:absolute}

/* header */
.topbar{left:0;top:0;width:1120px;height:69px;background:var(--yellow)}
.nav-left{left:91px;top:26px;display:flex;align-items:center;gap:12px;color:var(--white);font:400 15px "Roboto Condensed",sans-serif;letter-spacing:.3px}
.brand{left:0;width:1120px;top:14px;text-align:center;color:var(--white);font:700 34px/40px "Roboto Condensed",sans-serif;letter-spacing:-.5px}
.btn{top:23px;height:27px;width:75px;font:400 12px/25px "Roboto Condensed",sans-serif;text-align:center;color:var(--white);border-radius:2px}
.btn-signup{left:868px;background:var(--dark);border:1px solid var(--dark)}
.btn-login{left:953px;border:1px solid var(--white)}

/* hero */
.hero{left:0;top:69px;width:1120px;height:402px;background:linear-gradient(180deg,#4a4a4c 0%,#2a2d33 45%,#1c2028 100%)}
.hero-title{left:0;top:190px;width:1120px;text-align:center;color:var(--white);font:italic 400 48px "Roboto Condensed",sans-serif}

/* main card */
.card{left:92px;top:356px;width:935px;height:700px;background:var(--white);border-top:2px solid var(--accent-red);box-shadow:0 0 12px rgba(0,0,0,.15)}
.mission-title{left:108px;top:382px;font:400 29px "Roboto Condensed",sans-serif;color:var(--dark)}
.tabs{left:109px;top:434px;width:621px;height:41px;background:var(--panel);border:1px solid #ddd;display:flex;font:400 14px "Roboto Condensed",sans-serif;color:var(--dark)}
.tab{line-height:39px;text-align:center}
.tab.active{background:var(--yellow);color:var(--white);width:230px}
.tab-updates{width:150px}
.tab-comments{width:110px}
.progress-track{left:110px;top:505px;width:7px;height:531px;background:#eee;border-radius:4px}
.progress-fill{left:110px;top:505px;width:7px;height:98px;background:var(--yellow);border-radius:4px}
.story p{font-size:10.5px;line-height:19px;color:#555;margin-bottom:7px}
.story{left:142px;top:499px;width:580px}
.photo{left:142px;top:644px;width:588px;height:226px;background:linear-gradient(100deg,#1e3646 0%,#3a4b52 45%,#5a5a5c 70%,#2d3034 100%)}
.post-icon{left:142px;top:892px;width:36px;height:36px;border:1px solid var(--yellow);border-radius:50%}
.post-title{left:191px;top:886px;font:400 16px "Open Sans",sans-serif;color:#333}
.post-meta{left:193px;top:916px;display:flex;gap:22px;font:italic 400 9.5px "Open Sans",sans-serif;color:#666}
.post-body{left:144px;top:948px;width:612px;font-size:10.5px;line-height:19px;color:#555}
.read-more{left:144px;top:1020px;font-size:10.5px;color:#333}

/* sidebar */
.box{left:763px;width:243px;border:1px solid var(--yellow);background:var(--white)}
.box-head{background:var(--yellow);height:36px;padding-left:10px;font:400 17px/36px "Roboto Condensed",sans-serif;color:var(--dark)}
.box-name{top:385px;height:107px}
.pin{position:absolute;left:11px;top:55px;width:30px;height:30px;background:var(--dark);border-radius:3px}
.name-info{position:absolute;left:52px;top:52px;font-size:11.5px;line-height:18.5px;color:#666;letter-spacing:.3px}
.box-support{top:509px;height:179px}
.avatars{position:absolute;right:14px;top:9px;display:flex;gap:6px}
.support-now{position:absolute;left:13px;top:58px;font-size:12.5px;color:#444;letter-spacing:.4px}
.gauge{position:absolute;left:13px;top:89px}
.support-stats{position:absolute;left:89px;top:96px;font-size:11.5px;line-height:18.5px;color:#444;letter-spacing:.3px}
.box-participate{top:705px;height:231px}
.option{height:39px;border-top:1px solid #e4e4e4;display:flex;align-items:center;padding:0 13px;font-size:12px;color:#333;letter-spacing:.4px}
.option:nth-child(odd){background:#f5f5f5}
.check{width:14px;height:14px;border:1px solid #ccc;background:#f0f0f0;margin-right:7px}
.option .label{flex:1}
.amount{font-size:10px;color:#888;margin-right:28px}

/* footer */
.footer{left:0;top:1090px;width:1120px;height:110px;background:var(--dark)}
.social{left:479px;top:1115px;display:flex;gap:11px}
.social span{width:23px;height:23px;background:var(--white);border-radius:4px}
.copyright{left:0;width:1120px;top:1151px;text-align:center;color:var(--white);font-size:12px}
</style>
</head>
<body>

<header class="abs topbar"></header>
<div class="abs nav-left">
  <svg width="15" height="12" viewBox="0 0 15 12"><rect width="15" height="2.4" fill="#fff"/><rect y="4.8" width="15" height="2.4" fill="#fff"/><rect y="9.6" width="15" height="2.4" fill="#fff"/></svg>
  <span>SEE THE MISSION</span>
  <svg width="12" height="12" viewBox="0 0 12 12"><circle cx="5" cy="5" r="3.6" stroke="#fff" stroke-width="2" fill="none"/><line x1="7.6" y1="7.6" x2="11" y2="11" stroke="#fff" stroke-width="2"/></svg>
</div>
<div class="abs brand">HOPEWINGSRALLY</div>
<div class="abs btn btn-signup">SIGN UP</div>
<div class="abs btn btn-login">LOGIN</div>

<div class="abs hero" role="img" aria-label="Dusky city skyline at night"></div>
<h1 class="abs hero-title">Hope Wings Rally</h1>

<main class="abs card"></main>
<h2 class="abs mission-title">MISSION: ORPHAN MARIA, 11Y</h2>
<nav class="abs tabs">
  <div class="tab active">STORY</div>
  <div class="tab tab-updates">UPDATES</div>
  <div class="tab tab-comments">COMMENTS</div>
</nav>

<div class="abs progress-track"></div>
<div class="abs progress-fill"></div>

<div class="abs story">
  <p>Lorem ipsum dolor sit amet, consectetur adipiscing elit, sed do eiusmod tempor incididunt ut labore et dolore magna aliqua. Ut enim ad minim veniam, quis nostrud exercitation ullamco laboris nisi ut aliquip ex ea commodo consequat. Duis aute irure dolor in reprehenderit in voluptate velit esse cillum dolore eu fugiat nulla pariatur.....</p>
  <p>Lorem ipsum dolor sit amet, consectetur adipiscing elit, sed do eiusmod tempor incididunt ut labore et dolore magna aliqua. Ut enim ad minim veniam, quis nostrud exercitation ullamco laboris nisi ut aliquip ex ea commodo consequat. Duis aute irure dolor in reprehenderit in voluptate velit esse cillum dolore eu fugiat nulla pariatur.....</p>
</div>

<div class="abs photo" role="img" aria-label="Person holding a tablet showing a market chart"></div>

<div class="abs post-icon">
  <svg width="36" height="36" viewBox="0 0 36 36"><rect x="11" y="12" width="14" height="11" fill="none" stroke="#ffc400" stroke-width="1.5"/><polyline points="12,22 16,17 19,20 21,18 24,22" fill="none" stroke="#ffc400" stroke-width="1.3"/><circle cx="21" cy="15" r="1.3" fill="#ffc400"/></svg>
</div>
<h3 class="abs post-title">Nemo enim ipsam voluptatem quia voluptas</h3>
<div class="abs post-meta"><span>▦ March 25, 2015</span><span>◌ 2 comments</span><span>✎ by David</span></div>
<p class="abs post-body">Lorem ipsum dolor sit amet, consectetur adipiscing elit, sed do eiusmod tempor incididunt ut labore et dolore magna aliqua. Ut enim ad minim veniam, quis nostrud exercitation ullamco laboris nisi ut aliquip ex ea commodo consequat. Duis aute irure dolor in reprehenderit in voluptate velit esse cillum dolore eu fugiat nulla pariatur.....</p>
<a class="abs read-more">CONTINUE READING &gt;&gt;</a>

<aside class="abs box box-name">
  <div class="box-head">NAME: MARIA, 11Y</div>
  <div class="pin"><svg width="30" height="30" viewBox="0 0 30 30"><path d="M15 8a5 5 0 0 0-5 5c0 4 5 9 5 9s5-5 5-9a5 5 0 0 0-5-5z" fill="#fff"/><circle cx="15" cy="13" r="1.8" fill="#2b2b2b"/></svg></div>
  <div class="name-info">Kalkutta<br>Organization:Jacob</div>
</aside>

<aside class="abs box box-support">
  <div class="box-head">SUPPORT</div>
  <div class="avatars">
    <svg width="22" height="22" viewBox="0 0 22 22" role="img" aria-label="Supporter avatar"><rect x="4" y="4" width="14" height="14" transform="rotate(45 11 11)" fill="#8c7a6a" stroke="#fff" stroke-width="2"/></svg>
    <svg width="22" height="22" viewBox="0 0 22 22" role="img" aria-label="Supporter avatar"><rect x="4" y="4" width="14" height="14" transform="rotate(45 11 11)" fill="#9a8470" stroke="#fff" stroke-width="2"/></svg>
    <svg width="22" height="22" viewBox="0 0 22 22" role="img" aria-label="Supporter avatar"><rect x="4" y="4" width="14" height="14" transform="rotate(45 11 11)" fill="#6e6259" stroke="#fff" stroke-width="2"/></svg>
    <svg width="22" height="22" viewBox="0 0 22 22" role="img" aria-label="Supporter avatar"><rect x="4" y="4" width="14" height="14" transform="rotate(45 11 11)" fill="#a48e7c" stroke="#fff" stroke-width="2"/></svg>
  </div>
  <div class="support-now">My support is now:$5/month</div>
  <svg class="gauge" width="68" height="68" viewBox="0 0 68 68">
    <circle cx="34" cy="34" r="31" fill="none" stroke="#2b2b2b" stroke-width="3"/>
    <circle cx="34" cy="34" r="31" fill="none" stroke="#ffc400" stroke-width="3" stroke-dasharray="87.6 200" transform="rotate(90 34 34)"/>
    <text x="30" y="41" text-anchor="middle" font-family="Open Sans, sans-serif" font-size="18" fill="#333">45</text>
    <text x="45" y="41" font-family="Open Sans, sans-serif" font-size="6" fill="#333">%</text>
  </svg>
  <div class="support-stats">$15 GIVEN<br>of total $35 needed<br>per month need</div>
</aside>

<aside class="abs box box-participate">
  <div class="box-head">PARTICIPATE</div>
  <div class="options">
    <div class="option"><span class="check"></span><span class="label">I am in,$1/month</span><svg width="12" height="10" viewBox="0 0 12 10"><path d="M0 1h2l1.5 6h6.5l1-4.5H3" fill="none" stroke="#555" stroke-width="1"/><circle cx="4.5" cy="9" r=".9" fill="#555"/><circle cx="9" cy="9" r=".9" fill="#555"/></svg></div>
    <div class="option"><span class="check"></span><span class="label">Increased, $5/month</span><svg width="12" height="10" viewBox="0 0 12 10"><path d="M0 1h2l1.5 6h6.5l1-4.5H3" fill="none" stroke="#555" stroke-width="1"/><circle cx="4.5" cy="9" r=".9" fill="#555"/><circle cx="9" cy="9" r=".9" fill="#555"/></svg></div>
    <div class="option"><span class="check"></span><span class="label">Decent help,$10/month</span><svg width="12" height="10" viewBox="0 0 12 10"><path d="M0 1h2l1.5 6h6.5l1-4.5H3" fill="none" stroke="#555" stroke-width="1"/><circle cx="4.5" cy="9" r=".9" fill="#555"/><circle cx="9" cy="9" r=".9" fill="#555"/></svg></div>
    <div class="option"><span class="check"></span><span class="label">Whole kid,$35/month</span><svg width="12" height="10" viewBox="0 0 12 10"><path d="M0 1h2l1.5 6h6.5l1-4.5H3" fill="none" stroke="#555" stroke-width="1"/><circle cx="4.5" cy="9" r=".9" fill="#555"/><circle cx="9" cy="9" r=".9" fill="#555"/></svg></div>
    <div class="option"><span class="check"></span><span class="label">My amount</span><span class="amount">Enter amount</span><svg width="12" height="10" viewBox="0 0 12 10"><path d="M0 1h2l1.5 6h6.5l1-4.5H3" fill="none" stroke="#555" stroke-width="1"/><circle cx="4.5" cy="9" r=".9" fill="#555"/><circle cx="9" cy="9" r=".9" fill="#555"/></svg></div>
  </div>
</aside>

<footer class="abs footer"></footer>
<div class="abs social"><span></span><span></span><span></span><span></span><span></span></div>
<div class="abs copyright">Copyright @ 2015 - 2016 Hopewingsrally. All Rights Reserved.</div>

</body>
</html>
```